Firm Stationery Design

I need a design for stationery, including: Stationery First Page, Stationery Second Sheet, Envelope, Mailing Label for Flat Envelopes, and Business Cards

```html
<!DOCTYPE html>
<html lang="en">
<head>
<meta charset="utf-8">
<title>Hartwell Law LLC — Business Cards</title>
<link rel="stylesheet" href="https://fonts.googleapis.com/css2?family=Montserrat:wght@400;500;700;800&display=swap">
<style>
  :root {
    --backdrop: #232323;
    --card-dark: #2e2e2e;
    --band-dark: #1c1c1c;
    --paper: #ffffff;
    --accent: #f5a00f;
    --ink: #1b1b1b;
    --light-text: #f2f2f2;
    --rule-grey: #8a8a8a;
  }
  * { box-sizing: border-box; margin: 0; padding: 0; }
  html, body {
    width: 1200px; height: 689px; overflow: hidden;
    background: var(--backdrop);
    font-family: "Montserrat", Arial, sans-serif;
  }
  .canvas {
    position: relative; width: 1200px; height: 689px;
    display: flex; align-items: center; justify-content: center; gap: 40px;
  }
  .card {
    position: relative; width: 520px; height: 297px;
    border-radius: 14px; overflow: hidden; flex: none;
  }
  .card-front {
    background: var(--card-dark);
    display: flex; align-items: center; justify-content: center;
  }
  .wordmark { display: flex; align-items: center; gap: 14px; }
  .wordmark-square { width: 22px; height: 22px; background: var(--accent); flex: none; }
  .wordmark-name {
    font-weight: 800; font-size: 30px; letter-spacing: 1px;
    text-transform: uppercase; white-space: nowrap;
  }
  .card-front .wordmark-name { color: var(--light-text); }
  .card-back { background: var(--paper); }
  .back-top {
    height: 156px; display: flex; align-items: center; justify-content: center;
  }
  .card-back .wordmark-name { color: var(--ink); font-size: 26px; }
  .accent-rule { height: 4px; background: var(--accent); }
  .back-band {
    position: absolute; left: 0; right: 0; top: 160px; bottom: 0;
    background: var(--band-dark);
    display: flex; align-items: center; justify-content: center; gap: 22px;
    color: var(--light-text);
  }
  .person { text-align: right; white-space: nowrap; }
  .person-name {
    color: var(--accent); font-weight: 700; font-size: 21px;
    text-transform: uppercase; line-height: 1.15;
  }
  .person-role, .person-address { font-size: 12.5px; line-height: 1.4; }
  .divider { width: 1px; height: 82px; background: var(--rule-grey); flex: none; }
  .contacts { list-style: none; font-size: 12.5px; line-height: 1.55; white-space: nowrap; }
  .contacts li { display: flex; align-items: center; gap: 8px; }
  .contacts svg { width: 11px; height: 11px; flex: none; }
</style>
</head>
<body>
<main class="canvas">
  <section class="card card-front" aria-label="Business card front">
    <div class="wordmark">
      <span class="wordmark-square"></span>
      <span class="wordmark-name">Hartwell Law LLC</span>
    </div>
  </section>

  <section class="card card-back" aria-label="Business card back">
    <div class="back-top">
      <div class="wordmark">
        <span class="wordmark-square"></span>
        <span class="wordmark-name">Hartwell Law LLC</span>
      </div>
    </div>
    <div class="accent-rule"></div>
    <div class="back-band">
      <div class="person">
        <p class="person-name">Daniel Reed</p>
        <p class="person-role">President</p>
        <p class="person-address">4120 Alder Court<br>Fairbanks, Canada 21806</p>
      </div>
      <div class="divider"></div>
      <ul class="contacts">
        <li>
          <svg viewBox="0 0 12 12" aria-hidden="true"><path d="M2 1l2 0 1 3-1.3 1a7 7 0 0 0 3.3 3.3L8 7l3 1v2a1 1 0 0 1-1 1C5 11 1 7 1 2a1 1 0 0 1 1-1z" fill="var(--accent)"/></svg>
          555-210-4830
        </li>
        <li>
          <svg viewBox="0 0 12 12" aria-hidden="true"><rect x="3" y="0.8" width="6" height="10.4" rx="1" fill="none" stroke="var(--accent)" stroke-width="1.4"/></svg>
          555-318-2967
        </li>
        <li>
          <svg viewBox="0 0 12 12" aria-hidden="true"><rect x="0.5" y="2" width="11" height="8" fill="var(--accent)"/><path d="M0.5 2l5.5 4.5L11.5 2" fill="none" stroke="var(--band-dark)" stroke-width="1"/></svg>
          info@hartwell.com
        </li>
        <li>
          <svg viewBox="0 0 12 12" aria-hidden="true"><circle cx="6" cy="6" r="5" fill="none" stroke="var(--accent)" stroke-width="1.3"/><path d="M1 6h10M6 1c-2 2.5-2 7.5 0 10M6 1c2 2.5 2 7.5 0 10" fill="none" stroke="var(--accent)" stroke-width="1"/></svg>
          www.hartwell.com
        </li>
      </ul>
    </div>
  </section>
</main>
</body>
</html>
```